Residential Remodeling Contractor needs updated business card

I need a new design for my business card.
Name of the company is Ridgefell Construction. I need a card that commands presence, strength, integrity. I have been in business for 28 years. I am a Residential Remodeling Contractor that covers all aspects of a residential remodel and build.

```html
<!DOCTYPE html>
<html lang="en">
<head>
<meta charset="utf-8">
<title>Ridgefell Construction – Business Card</title>
<link rel="stylesheet" href="https://fonts.googleapis.com/css2?family=Cinzel:wght@400;600&family=Poppins:wght@300;400&display=swap">
<style>
  :root {
    --backdrop: #a6a6a6;
    --card-blue: #1f3c7e;
    --ink-white: #ffffff;
    --rule-white: rgba(255, 255, 255, 0.75);
    --card-shadow: rgba(0, 0, 0, 0.35);
  }
  * { box-sizing: border-box; margin: 0; padding: 0; }
  html, body {
    width: 1200px;
    height: 820px;
    overflow: hidden;
    background: var(--backdrop);
  }
  .canvas {
    position: relative;
    width: 1200px;
    height: 820px;
    display: flex;
    align-items: center;
    justify-content: center;
    gap: 50px;
  }
  .card {
    position: relative;
    width: 525px;
    height: 300px;
    background: var(--card-blue);
    color: var(--ink-white);
    box-shadow: 0 10px 24px var(--card-shadow);
  }

  /* Back: contact side */
  .card--contact {
    display: flex;
    flex-direction: column;
    align-items: center;
    justify-content: center;
    text-align: center;
    font-family: "Poppins", sans-serif;
  }
  .contact__name {
    font-family: "Cinzel", serif;
    font-weight: 400;
    font-size: 23px;
    letter-spacing: 0.5px;
    line-height: 1.1;
  }
  .contact__role {
    font-weight: 400;
    font-size: 13px;
    letter-spacing: 0.4px;
    text-transform: uppercase;
    margin-top: 2px;
  }
  .contact__rule {
    width: 82px;
    height: 1px;
    background: var(--rule-white);
    margin: 14px 0;
  }
  .contact__lines {
    font-size: 14px;
    font-weight: 300;
    line-height: 1.35;
    list-style: none;
  }

  /* Front: brand side */
  .card--brand {
    font-family: "Cinzel", serif;
  }
  .brand {
    position: absolute;
    left: 120px;
    top: 78px;
    display: flex;
    align-items: center;
    gap: 18px;
  }
  .brand__dot {
    width: 30px;
    height: 30px;
    border-radius: 50%;
    background: var(--ink-white);
    flex: none;
  }
  .brand__name {
    font-weight: 400;
    line-height: 1.02;
  }
  .brand__name-main {
    display: block;
    font-size: 42px;
    letter-spacing: 1px;
  }
  .brand__name-sub {
    display: block;
    font-size: 34px;
    letter-spacing: 1px;
  }
  .brand__since {
    position: absolute;
    left: 0;
    right: 0;
    top: 196px;
    text-align: center;
    padding-left: 110px;
    font-size: 12px;
    letter-spacing: 0.6px;
  }
  .brand__tagline {
    position: absolute;
    left: 0;
    right: 0;
    top: 222px;
    text-align: center;
    padding-left: 40px;
    font-size: 13px;
    letter-spacing: 0.8px;
  }
</style>
</head>
<body>
<main class="canvas">

  <section class="card card--contact" aria-label="Business card, contact side">
    <h2 class="contact__name">Daniel Hartwell</h2>
    <p class="contact__role">Managing Director</p>
    <div class="contact__rule"></div>
    <ul class="contact__lines">
      <li>055-310 742 618</li>
      <li>info@ridgefellbuild.com</li>
      <li>www.ridgefellbuild.com</li>
    </ul>
    <div class="contact__rule"></div>
    <ul class="contact__lines">
      <li>86, Harbor Ridge Road</li>
      <li>30718, Northvale</li>
    </ul>
  </section>

  <section class="card card--brand" aria-label="Business card, brand side">
    <div class="brand">
      <span class="brand__dot" aria-hidden="true"></span>
      <h1 class="brand__name">
        <span class="brand__name-main">Ridgefell</span>
        <span class="brand__name-sub">Construction</span>
      </h1>
    </div>
    <p class="brand__since">Since 28 years</p>
    <p class="brand__tagline">Residential contractor for remodeling and build</p>
  </section>

</main>
</body>
</html>
```